"Vine Hollow Excursions" is a top notch Santa Barbara County Wine Tour company.

We provide scenic, boutique and custom wine tours. I need the card to be clean and classy. I will provide our logo. I would like the logo to cover the back side of the card as an option and would like to see a couple color options other then our signature green and gold. I would like to see some creative options and let the designers come up with options.
I need cards for myself and my team. The final design should communicate "An authentic and boutique wine tour experience"
Please use my website for reference www.vinehollowexcursions.example

Target Market(s)

We have a wide range of clients from millennials to baby boomers

Industry/Entity Type

Tour

Contact Information for Business Card

Contact info:
Dale Morton
805-219-6384
info@vinehollowexcursions.example
vinehollowexcursions.example

Colors

Designer to choose colors to be used in the design.

Requirements
Must have
• my logo
Nice to have
• *I would like to have the backside side with the logo and the company statement
• "An authentic and boutique wine tour experience" as an option.
• *I would also like to see what the designers can create!
• *I would like to see an option that incorporates or social: instagram, yelp, trip advisor
Should not have
• I do not want it too busy.

```html
<!DOCTYPE html>
<html lang="en">
<head>
<meta charset="utf-8">
<title>Vine Hollow Excursions – Business Card</title>
<link rel="stylesheet" href="https://fonts.googleapis.com/css2?family=Cinzel:wght@500;600&family=Lato:wght@400;700&display=swap">
<style>
  :root {
    --bg: #e4e4e4;
    --green: #43674a;
    --green-dark: #35553c;
    --gold: #a89a86;
    --taupe: #a99a86;
    --ink: #3a3a3a;
    --white: #ffffff;
    --rule: #8c8c8c;
  }
  * { box-sizing: border-box; margin: 0; padding: 0; }
  html, body { width: 1200px; height: 800px; overflow: hidden; background: var(--bg); }
  .canvas {
    width: 1200px; height: 800px;
    display: flex; align-items: center; justify-content: center; gap: 56px;
  }
  .card {
    position: relative;
    width: 520px; height: 298px;
    box-shadow: 0 10px 28px rgba(0,0,0,.16);
    overflow: hidden;
  }

  /* Front */
  .card--front { background: var(--white); }
  .front-brand {
    position: absolute; left: 34px; top: 0; width: 210px; height: 270px;
    display: flex; align-items: center; gap: 10px;
  }
  .brand-mark { width: 12px; height: 12px; border-radius: 50%; background: var(--green); flex: none; }
  .brand-name {
    font-family: "Cinzel", serif; font-weight: 600; font-size: 21px; line-height: 1.15;
    color: var(--green); letter-spacing: .02em;
  }
  .front-divider {
    position: absolute; left: 262px; top: 60px; width: 1px; height: 118px; background: var(--rule);
  }
  .contact { position: absolute; left: 284px; top: 58px; }
  .contact-name {
    font-family: "Cinzel", serif; font-weight: 600; font-size: 20px; color: var(--green);
    letter-spacing: .02em;
  }
  .contact-title {
    font-family: "Lato", sans-serif; font-size: 12.5px; color: var(--ink);
    letter-spacing: .04em; margin: 2px 0 12px;
  }
  .contact-list { list-style: none; font-family: "Lato", sans-serif; font-size: 11.5px; color: var(--ink); }
  .contact-list li { display: flex; align-items: center; gap: 9px; margin-bottom: 4px; }
  .contact-list svg { width: 10px; height: 10px; flex: none; fill: var(--green); }
  .contact-list strong { font-weight: 700; }
  .front-band { position: absolute; left: 0; right: 0; bottom: 0; height: 14px; background: var(--taupe); }
  .front-social {
    position: absolute; right: 0; bottom: 14px; height: 40px; width: 170px;
    background: var(--white); border-top: 6px solid var(--green);
    display: flex; align-items: center; gap: 7px; padding-left: 16px;
    font-family: "Lato", sans-serif; font-size: 11px; color: var(--ink);
  }
  .social-dot { width: 8px; height: 8px; background: var(--green); border-radius: 50%; flex: none; }

  /* Back */
  .card--back { background: var(--green); }
  .back-brand {
    position: absolute; inset: 0 0 40px 0;
    display: flex; align-items: center; justify-content: center; gap: 12px;
  }
  .back-brand .brand-mark { background: var(--white); width: 14px; height: 14px; }
  .back-brand .brand-name { color: var(--white); font-size: 26px; text-align: center; }
  .back-social {
    position: absolute; right: 26px; bottom: 22px;
    display: flex; gap: 14px; align-items: center;
    font-family: "Lato", sans-serif; font-size: 11px; color: var(--white);
  }
  .back-social span { display: flex; align-items: center; gap: 6px; }
  .back-social .social-dot { background: var(--white); }
</style>
</head>
<body>
<main class="canvas">
  <section class="card card--front" aria-label="Business card front">
    <div class="front-brand">
      <span class="brand-mark"></span>
      <span class="brand-name">Vine Hollow<br>Excursions</span>
    </div>
    <div class="front-divider"></div>
    <div class="contact">
      <p class="contact-name">DALE MORTON</p>
      <p class="contact-title">TRIP ADVISOR</p>
      <ul class="contact-list">
        <li><svg viewBox="0 0 10 10"><path d="M2 0.5l2 2-1 1.3c.6 1.3 1.6 2.3 2.9 2.9l1.3-1 2 2-1.3 1.6C4.3 9 1 5.7.3 1.8z"/></svg>805-219-6384</li>
        <li><svg viewBox="0 0 10 10"><path d="M0 2h10v6H0z M1 3v.4l4 2.4 4-2.4V3z" fill-rule="evenodd"/></svg>info@vinehollowexcursions.example</li>
        <li><svg viewBox="0 0 10 10"><circle cx="5" cy="5" r="4.6"/></svg>www.<strong>vinehollowexcursions</strong>.example</li>
      </ul>
    </div>
    <div class="front-social"><span class="social-dot"></span>/vinehollowexcursions</div>
    <div class="front-band"></div>
  </section>

  <section class="card card--back" aria-label="Business card back">
    <div class="back-brand">
      <span class="brand-mark"></span>
      <span class="brand-name">Vine Hollow<br>Excursions</span>
    </div>
    <div class="back-social">
      <span><span class="social-dot"></span>/biz/vinehollowexcursions</span>
      <span><span class="social-dot"></span>@vhxwinetours</span>
    </div>
  </section>
</main>
</body>
</html>
```